Business Card Design for Marketing Firm

Looking for business card design for higher end marketing firm. Clean but impressionable/trendy. We are a marketing firm that represents manufacturers in the foodservice equipment and supply industry. Our customers are end users such has hotels, restaurants, country clubs, convention centers and casinos as well as distributors of restaurants supplies and equipment, and manufacturers of foodservice equipment and supplies.
Target Market(s)
Hotels, Restaurants, Supply & Equipment Distributors, Foodservice Manufacturers
Industry/Entity Type
Foodservice/Hospitality
Contact Information for Business Card
Name, Title, Contact Number, Email, Website, Social Media, Address
Requirements
Must have
- Clean & Simple but Serious and Impressionable

```html
<!DOCTYPE html>
<html lang="en">
<head>
<meta charset="utf-8">
<title>Meridian Hospitality Reps — Business Card</title>
<link href="https://fonts.googleapis.com/css2?family=Cinzel:wght@500&family=Montserrat:wght@500;800&display=swap" rel="stylesheet">
<style>
  :root {
    --navy: #2b2a7a;
    --navy-deep: #232266;
    --white: #ffffff;
    --grey: #b3b4b6;
    --ink: #1c1c24;
    --stage: #e9e9ec;
  }
  * { box-sizing: border-box; margin: 0; padding: 0; }
  html, body { width: 1200px; height: 900px; overflow: hidden; }
  body { background: var(--stage); position: relative; font-family: "Montserrat", sans-serif; }

  .card {
    position: absolute;
    width: 560px;
    height: 320px;
    border-radius: 22px;
    overflow: hidden;
    box-shadow: 0 10px 26px rgba(0,0,0,.18);
  }
  .card--back { left: 70px; top: 80px; background: var(--navy); }
  .card--front { left: 570px; top: 500px; background: var(--white); }

  .brand {
    position: absolute;
    display: flex;
    align-items: center;
    gap: 14px;
    font-family: "Cinzel", serif;
    font-weight: 500;
    letter-spacing: .04em;
    line-height: 1.15;
  }
  .brand__dot { flex: none; border-radius: 50%; }
  .brand__name span { display: block; }

  .card--back .brand { left: 0; right: 0; top: 0; bottom: 0; justify-content: center; color: var(--white); font-size: 30px; }
  .card--back .brand__dot { width: 22px; height: 22px; background: var(--white); }

  .card--front .brand { left: 28px; top: 112px; width: 210px; color: var(--navy); font-size: 21px; gap: 10px; }
  .card--front .brand__dot { width: 14px; height: 14px; background: var(--navy); }

  .divider { position: absolute; left: 258px; top: 58px; width: 1.5px; height: 150px; background: var(--navy); }

  .contact { position: absolute; left: 276px; top: 46px; color: var(--ink); font-size: 12.5px; line-height: 1.35; }
  .contact__name { color: var(--navy); font-weight: 800; font-size: 19px; letter-spacing: .01em; }
  .contact__role { margin-bottom: 6px; }
  .contact__address { margin-bottom: 6px; }
  .contact__row { display: flex; align-items: center; gap: 8px; }
  .contact__row svg { width: 13px; height: 13px; flex: none; fill: var(--navy); }
  .contact__social-dot { width: 13px; height: 13px; border-radius: 50%; background: var(--navy); flex: none; }

  .wave { position: absolute; left: 0; bottom: 0; width: 560px; height: 320px; }
</style>
</head>
<body>

  <section class="card card--back" aria-label="Card back">
    <div class="brand">
      <span class="brand__dot"></span>
      <div class="brand__name"><span>Meridian Hospitality</span><span>Reps</span></div>
    </div>
  </section>

  <section class="card card--front" aria-label="Card front">
    <svg class="wave" viewBox="0 0 560 320" preserveAspectRatio="none" aria-hidden="true">
      <path d="M40 320 C120 300 260 300 340 240 C420 180 460 150 560 135 L560 320 Z" fill="#b3b4b6"/>
      <path d="M40 320 C130 306 270 308 352 250 C430 196 470 168 560 152 L560 320 Z" fill="#ffffff"/>
      <path d="M40 320 C135 312 280 316 360 258 C436 204 478 180 560 166 L560 320 Z" fill="#2b2a7a"/>
    </svg>

    <div class="brand">
      <span class="brand__dot"></span>
      <div class="brand__name"><span>Meridian Hospitality</span><span>Reps</span></div>
    </div>

    <div class="divider"></div>

    <div class="contact">
      <p class="contact__name">DANIEL HARTWELL</p>
      <p class="contact__role">Co-Founder</p>
      <p class="contact__address">P.O. BOX 45-12 EST-30<br>Linden Ave 14, Fairview</p>
      <p class="contact__row">
        <svg viewBox="0 0 24 24"><path d="M6.6 10.8a15.1 15.1 0 0 0 6.6 6.6l2.2-2.2a1 1 0 0 1 1-.25 11.4 11.4 0 0 0 3.6.57 1 1 0 0 1 1 1V20a1 1 0 0 1-1 1A17 17 0 0 1 3 4a1 1 0 0 1 1-1h3.5a1 1 0 0 1 1 1c0 1.25.2 2.45.57 3.57a1 1 0 0 1-.25 1z"/></svg>
        555-014-2290
      </p>
      <p class="contact__row">
        <svg viewBox="0 0 24 24"><path d="M2 5h20v14H2z M3.5 6.5 12 13l8.5-6.5" fill="none" stroke="#2b2a7a" stroke-width="2"/></svg>
        info@meridianhospitality.com
      </p>
      <p class="contact__row">
        <svg viewBox="0 0 24 24"><circle cx="12" cy="12" r="9" fill="none" stroke="#2b2a7a" stroke-width="2"/><path d="M3 12h18M12 3c3 3 3 15 0 18M12 3c-3 3-3 15 0 18" fill="none" stroke="#2b2a7a" stroke-width="1.6"/></svg>
        www.meridianhospitality.com
      </p>
      <p class="contact__row">
        <span class="contact__social-dot"></span>
        @meridianhospitality
      </p>
    </div>
  </section>

</body>
</html>
```